Veldmark Supplies Business Card

Professional business card that stand out to our potential customers. Front and back with clean modern design

Industry/Entity Type

Oil and gas

Contact Information for Business Card

Name, address, website , office phone and cell number

Requirements
Must have
• Editable files for each employee

```html
<!DOCTYPE html>
<html lang="en">
<head>
<meta charset="utf-8">
<title>Veldmark Supplies Business Card</title>
<link href="https://fonts.googleapis.com/css2?family=Roboto:wght@400;500;700&display=swap" rel="stylesheet">
<style>
  :root {
    --stage: #2a2a2a;
    --brand-red: #e01f26;
    --brand-blue: #1fa8d0;
    --paper: #ffffff;
    --ink: #2b2b2b;
  }
  html, body {
    margin: 0;
    width: 1200px;
    height: 852px;
    overflow: hidden;
    background: var(--stage);
    font-family: "Roboto", Arial, sans-serif;
  }
  .card {
    position: absolute;
    top: 283px;
    width: 500px;
    height: 286px;
    border-radius: 28px;
    overflow: hidden;
    box-sizing: border-box;
  }
  /* Back side */
  .card-back {
    left: 70px;
    background: linear-gradient(45deg, var(--brand-blue) 0%, #7a5a78 50%, var(--brand-red) 100%);
    display: flex;
    flex-direction: column;
    align-items: center;
    justify-content: center;
    gap: 18px;
  }
  .back-mark {
    width: 62px;
    height: 62px;
    border: 5px solid var(--paper);
    box-sizing: border-box;
  }
  .back-name {
    color: var(--paper);
    font-weight: 700;
    font-size: 28px;
    letter-spacing: 2px;
    text-transform: uppercase;
  }
  /* Front side */
  .card-front {
    left: 630px;
    background: var(--paper);
  }
  .front-wave {
    position: absolute;
    inset: 0;
  }
  .front-mark {
    position: absolute;
    left: 32px;
    top: 110px;
    width: 58px;
    height: 58px;
    background: var(--brand-red);
  }
  .front-name {
    position: absolute;
    left: 108px;
    top: 26px;
    color: var(--brand-red);
    font-weight: 700;
    font-size: 24px;
    letter-spacing: 1.5px;
    text-transform: uppercase;
    white-space: nowrap;
  }
  .person {
    position: absolute;
    left: 108px;
    top: 126px;
  }
  .person-name {
    color: var(--brand-blue);
    font-weight: 700;
    font-size: 19px;
    margin: 0;
  }
  .person-role {
    color: var(--ink);
    font-size: 12px;
    margin: 2px 0 0;
  }
  .contact {
    position: absolute;
    right: 26px;
    top: 156px;
    margin: 0;
    padding: 0;
    list-style: none;
    color: var(--paper);
    font-size: 11.5px;
    line-height: 19px;
    text-align: right;
  }
  .contact li {
    display: flex;
    justify-content: flex-end;
    align-items: center;
    gap: 7px;
    white-space: nowrap;
  }
  .contact svg { width: 10px; height: 10px; }
</style>
</head>
<body>

<section class="card card-back" aria-label="Card back">
  <div class="back-mark"></div>
  <div class="back-name">Veldmark Supplies</div>
</section>

<section class="card card-front" aria-label="Card front">
  <svg class="front-wave" viewBox="0 0 500 286" preserveAspectRatio="none" aria-hidden="true">
    <path d="M0 240 C150 234 250 220 320 168 C370 130 430 102 500 94 L500 286 L0 286 Z" fill="var(--brand-red)"/>
    <path d="M0 228 C150 222 245 208 310 158 C360 120 425 92 500 84" fill="none" stroke="var(--brand-blue)" stroke-width="7"/>
    <path d="M140 226 C220 216 270 192 305 160" fill="none" stroke="var(--brand-blue)" stroke-width="3"/>
  </svg>

  <div class="front-mark"></div>
  <div class="front-name">Veldmark Supplies</div>

  <div class="person">
    <p class="person-name">Marcus Hale</p>
    <p class="person-role">Managing Director</p>
  </div>

  <ul class="contact">
    <li>(555)014-0287
      <svg viewBox="0 0 10 10"><path d="M2 1h2l1 2.5-1.2 1a6 6 0 0 0 2.7 2.7l1-1.2L10 7v2a1 1 0 0 1-1 1A9 9 0 0 1 0 2a1 1 0 0 1 1-1z" fill="var(--paper)"/></svg>
    </li>
    <li>www.veldmarksupplies.com
      <svg viewBox="0 0 10 10"><circle cx="5" cy="5" r="4.2" fill="none" stroke="var(--paper)" stroke-width="1.2"/><path d="M1 5h8M5 1v8" stroke="var(--paper)" stroke-width="1"/></svg>
    </li>
    <li>sales@veldmarksupplies.com
      <svg viewBox="0 0 10 10"><rect x="0.5" y="2" width="9" height="6.5" fill="none" stroke="var(--paper)" stroke-width="1.2"/><path d="M0.5 2l4.5 3.5L9.5 2" fill="none" stroke="var(--paper)" stroke-width="1.2"/></svg>
    </li>
    <li>415 W. Harlan Ave Suite 3 Midland, Tx 79701
      <svg viewBox="0 0 10 10"><path d="M5 0.5a3.3 3.3 0 0 1 3.3 3.3C8.3 6.3 5 9.5 5 9.5S1.7 6.3 1.7 3.8A3.3 3.3 0 0 1 5 0.5z" fill="var(--paper)"/></svg>
    </li>
  </ul>
</section>

</body>
</html>
```